Brightfield Ventures Inc. Letterhead

Creation of attractive and eye catching letterhead for a business start-up for the construction industry. Letterhead must relate to construction, but avoid standard hammer and tools in the design.

I forgot to add some details, sorry about that. Some pertinent info: Ph: 916-555-0187 brightfieldventures.example 448 Willowmere Ave, Ste 210 Folsom, CA 95999 info@brightfieldventures.example not sure if slogan should be in there" “Connecting construction professionals to create a purpose driven industry.” must be able to be used in word. Thanks!

```html
<!DOCTYPE html>
<html lang="en">
<head>
<meta charset="utf-8">
<title>Brightfield Ventures Inc. Letterhead</title>
<link href="https://fonts.googleapis.com/css2?family=Open+Sans:wght@400;600;700&display=swap" rel="stylesheet">
<style>
  :root {
    --navy: #0f1f5c;
    --red: #c8101a;
    --ink: #2b2b2b;
    --paper: #ffffff;
    --backdrop: #e9eaec;
    --rule: #9aa0b8;
  }
  * { box-sizing: border-box; margin: 0; padding: 0; }
  html, body {
    width: 1200px; height: 784px; overflow: hidden;
    background: var(--backdrop);
    font-family: "Open Sans", Arial, sans-serif;
  }
  .letterhead {
    position: absolute; left: 320px; top: 24px;
    width: 560px; height: 736px;
    background: var(--paper);
    box-shadow: 0 4px 18px rgba(0,0,0,.12);
    overflow: hidden;
  }
  .header-bands, .footer-bands { position: absolute; left: 0; width: 100%; }
  .header-bands { top: 0; height: 60px; }
  .footer-bands { bottom: 0; height: 40px; }
  .contact-list {
    position: absolute; top: 9px; right: 22px;
    list-style: none; color: #fff; font-size: 6.5px; line-height: 9px;
  }
  .contact-list li { display: flex; align-items: center; gap: 4px; }
  .contact-list svg { width: 6px; height: 6px; fill: #fff; }
  .brand {
    position: absolute; top: 88px; left: 40px;
    display: flex; align-items: center; gap: 7px;
    color: var(--navy); font-weight: 700; font-size: 14px; letter-spacing: .3px;
  }
  .brand-mark { width: 14px; height: 14px; background: var(--red); }
  .letter-body {
    position: absolute; top: 150px; left: 56px; width: 400px;
    color: var(--ink); font-size: 10px; line-height: 13.5px;
  }
  .salutation { font-weight: 700; font-size: 12px; margin-bottom: 10px; }
  .letter-body p { margin-bottom: 11px; }
  .signature {
    width: 110px; height: 48px; margin-top: 6px;
    background: linear-gradient(90deg, #f3f3f5, #e6e7ea);
    border-radius: 4px;
  }
  .footer-rule {
    position: absolute; left: 40px; right: 40px; bottom: 66px;
    height: 1px; background: var(--rule);
  }
  .footer-address {
    position: absolute; right: 40px; bottom: 48px;
    font-size: 7.5px; color: var(--ink);
  }
</style>
</head>
<body>
  <main class="letterhead">
    <svg class="header-bands" viewBox="0 0 560 60" preserveAspectRatio="none" aria-hidden="true">
      <path d="M0 0 H300 V30 Q300 40 290 40 H270 Q262 40 258 28 L255 18 H0 Z" fill="var(--navy)"/>
      <path d="M255 0 H560 V44 H292 Q284 44 282 36 L280 24 Q278 18 270 18 Z" fill="var(--red)"/>
      <path d="M255 0 H295 V6 H255 Z" fill="var(--navy)"/>
    </svg>
    <ul class="contact-list">
      <li><svg viewBox="0 0 10 10"><path d="M2 0 L4 2 L3 3.5 Q4 6 6.5 7 L8 6 L10 8 L8.5 10 Q2 9 0 1.5 Z"/></svg>916-555-0187</li>
      <li><svg viewBox="0 0 10 10"><path d="M0 2 H10 V8 H0 Z M0 2 L5 6 L10 2" /></svg>info@brightfieldventures.example</li>
      <li><svg viewBox="0 0 10 10"><circle cx="5" cy="5" r="5"/></svg>brightfieldventures.example</li>
    </ul>

    <div class="brand"><span class="brand-mark"></span>Brightfield Ventures Inc.</div>

    <section class="letter-body">
      <p class="salutation">Dear Mr. Ellison,</p>
      <p>Lorem Ipsum is simply dummy text of the printing and typesetting industry. Lorem Ipsum has been the industry's standard dummy text ever since the 1500s, when an unknown printer took a galley of type and scrambled it to make a type specimen book. It has survived not only five centuries, but also the leap into electronic typesetting, remaining essentially unchanged.</p>
      <p>The standard chunk of Lorem Ipsum used since the 1500s is reproduced below for those interested. Sections 1.10.32 and 1.10.33 from "de Finibus Bonorum et Malorum" by Cicero are also reproduced in their exact original form, accompanied by English versions from the 1914 translation by H. Rackham.</p>
      <p>Lorem Ipsum is simply dummy text of the printing and typesetting industry. Lorem Ipsum has been the industry's standard dummy text ever since the 1500s, when an unknown printer took a galley of type and scrambled it to make a type specimen book. It has survived not only five centuries, but also the leap into electronic typesetting, remaining essentially unchanged. It was popularised in the</p>
      <p>The standard chunk of Lorem Ipsum used since the 1500s is reproduced below for those interested. Sections 1.10.32 and 1.10.33 from "de Finibus Bonorum et Malorum" by Cicero are also reproduced in their exact original form, accompanied by English versions from the 1914 translation by H. Rackham.</p>
      <p>The standard chunk of Lorem Ipsum used since the 1500s is reproduced below for those interested. Sections 1.10.32 and 1.10.33 from "de Finibus Bonorum et Malorum" by Cicero are</p>
      <div class="signature" role="img" aria-label="Handwritten signature"></div>
    </section>

    <div class="footer-rule"></div>
    <p class="footer-address">448 Willowmere Ave, Ste 210, Folsom, CA 95999</p>
    <svg class="footer-bands" viewBox="0 0 560 40" preserveAspectRatio="none" aria-hidden="true">
      <path d="M300 40 L320 26 H560 V40 Z" fill="var(--red)"/>
      <path d="M322 24 L334 16 H560 V22 H326 Z" fill="var(--navy)"/>
    </svg>
  </main>
</body>
</html>
```